Design concept Visual UI of future mobile app - healthcare

Hi,
I'm looking for a top designer, innovative with strong experience in user interface

The app will be connected to a future health website related to depression and addiction by helping the user to track the moods, tired, anxiety using this mobile app.

I attached the deck of the overall project but I can send you a specific presentation for the app only

thanks

Target Market(s)

Switzerland, UK, Germany and France

Industry/Entity Type

Mental Health

Logo Text

Health, hope

Font styles to use
Sans Serif

Colors
cee9f5
33a6d7
0692cd
0255a3
3276b5
85abd2

Requirements
Must have
• keep it simple, easy to navigate
• The user should be able to track the moods on a daily basis,
• sleep time, and rate how the feel on the day
• To be able to get information from the sync deck of vexlo
Nice to have
• to be able share this app with a friend

```html
<!DOCTYPE html>
<html lang="en">
<head>
<meta charset="utf-8">
<title>Mood Tracker App Screens</title>
<link rel="stylesheet" href="https://fonts.googleapis.com/css2?family=Roboto:wght@400;500;700&display=swap">
<style>
  :root{
    --page:#f2f2f2;
    --ice:#cee9f5;
    --sky:#33a6d7;
    --ocean:#0692cd;
    --navy:#0255a3;
    --steel:#3276b5;
    --mist:#85abd2;
    --menu-top:#c4e5f3;
    --menu-bottom:#b3dced;
    --active:#8fd4f0;
    --content:#e6e6e6;
    --ink:#1f1f1f;
    --white:#ffffff;
    --heat-hot:#e8401f;
    --heat-warm:#e8a020;
    --heat-cool:#6f8a2a;
    --heat-deep:#556b24;
  }
  *{box-sizing:border-box;margin:0;padding:0}
  html,body{width:1200px;height:800px;overflow:hidden;background:var(--page);font-family:"Roboto",sans-serif}
  .screen{position:absolute;top:228px;width:189px;height:334px;overflow:hidden;background:var(--content)}
  .screen--graphs{left:233px}
  .screen--messages{left:510px}
  .screen--profile{left:786px}

  .status-bar{position:absolute;left:0;top:0;width:100%;height:13px;background:var(--ink);color:var(--white);font-size:5.5px;display:flex;align-items:center;justify-content:space-between;padding:0 5px}
  .status-bar--light{background:var(--white);color:var(--ink)}
  .status-time{position:absolute;left:50%;transform:translateX(-50%)}
  .battery{display:inline-block;width:12px;height:5px;background:currentColor;border-radius:1px;margin-left:2px;vertical-align:middle}

  .app-header{position:absolute;left:0;top:13px;width:100%;height:29px;background:var(--ice);display:flex;align-items:center}
  .menu-toggle{position:absolute;left:20px;top:10px;width:12px;height:9px;display:flex;flex-direction:column;justify-content:space-between}
  .menu-toggle span{height:2px;background:var(--steel)}
  .nav-arrow{position:absolute;top:9px;color:var(--steel);font-size:9px;line-height:1}
  .nav-arrow--back{left:38px}
  .nav-arrow--next{left:161px}
  .header-title{width:100%;text-align:center;color:var(--steel);font-size:8px;letter-spacing:.2px;padding-left:16px}
  .header-title--bold{font-weight:500}

  .side-menu{position:absolute;left:0;top:42px;width:114px;height:292px;background:linear-gradient(var(--menu-top),var(--menu-bottom))}
  .menu-item{position:absolute;left:12px;color:var(--steel);font-size:8.5px;font-weight:700;display:flex;align-items:center;gap:4px}
  .menu-item svg{width:7px;height:7px;fill:var(--steel)}
  .menu-sub{position:absolute;left:22px;color:var(--sky);font-size:6px}
  .menu-active{position:absolute;left:0;top:68px;width:114px;height:16px;background:var(--active)}

  .chart{position:absolute}
  .chart-label{position:absolute;font-size:4px;color:#666}

  .avatar{position:absolute;background:linear-gradient(160deg,#e6c9a2,#b98e66 60%,#8a6d55);border-radius:2px}
  .avatar--framed{border:2px solid var(--white);box-shadow:0 1px 2px rgba(0,0,0,.2)}
  .bubble{position:absolute;background:var(--white);border-radius:5px;box-shadow:0 1px 2px rgba(0,0,0,.15);padding:5px 0 0 6px;white-space:nowrap}
  .bubble-time{display:block;color:var(--ocean);font-size:3.8px;margin-bottom:4px}
  .bubble-text{display:block;color:var(--ink);font-size:4.2px}
  .bubble-tail{position:absolute;width:8px;height:40px;background:var(--white);border-radius:4px 0 0 4px}

  .profile-initial{position:absolute;left:183px;top:44px;color:var(--steel);font-size:8px}
  .action-button{position:absolute;left:141px;width:60px;height:15px;background:linear-gradient(var(--steel),var(--navy));color:var(--white);font-size:6.5px;display:flex;align-items:center;gap:4px;padding-left:7px;border-radius:1px}
  .action-button svg{width:7px;height:7px;fill:var(--white)}
  .section-title{position:absolute;left:133px;color:var(--steel);font-size:8px;white-space:nowrap}
  .contact-list{position:absolute;left:141px;width:60px;background:#ececec;border-left:1px solid #cfcfcf}
  .contact-list li{list-style:none;height:20px;border-bottom:1px solid #bdbdbd;font-size:5.5px;color:#8a8a8a;display:flex;align-items:center;padding-left:5px;white-space:nowrap}
</style>
</head>
<body>

<!-- Tracking graphs screen -->
<section class="screen screen--graphs">
  <div class="status-bar"><span>●●●○○ NOVA</span><span class="status-time">4:21 PM</span><span>100%<i class="battery"></i></span></div>
  <header class="app-header">
    <div class="menu-toggle"><span></span><span></span><span></span></div>
    <span class="nav-arrow nav-arrow--back">‹</span>
    <h1 class="header-title">TRACKING GRAPHS</h1>
    <span class="nav-arrow nav-arrow--next">›</span>
  </header>
  <nav class="side-menu">
    <div class="menu-active"></div>
    <div class="menu-item" style="top:7px"><svg viewBox="0 0 10 10"><path d="M5 0 10 5H8.5V10H6V7H4V10H1.5V5H0z"/></svg>HOME</div>
    <div class="menu-sub" style="top:24px">How do you feel today ?</div>
    <div class="menu-sub" style="top:39px">TRACKING GRAPHS</div>
    <div class="menu-sub" style="top:54px">PERSONAL INFORMATION</div>
    <div class="menu-item" style="top:72px"><svg viewBox="0 0 10 10"><path d="M0 2H7V3H1V9H7V6H8V10H0zM9 0 10 1 5 6H4V5z"/></svg>ACTIVITY</div>
    <div class="menu-item" style="top:92px"><svg viewBox="0 0 10 10"><path d="M0 4 5 1 10 4V10H0zM1 5V9H9V5L5 7z"/></svg>MESSAGES</div>
    <div class="menu-item" style="top:113px"><svg viewBox="0 0 10 10"><circle cx="5" cy="3" r="2.5"/><path d="M0 10C0 6 10 6 10 10z"/></svg>PROFILE</div>
    <div class="menu-item" style="top:134px"><svg viewBox="0 0 10 10"><circle cx="5" cy="5" r="4"/><circle cx="5" cy="5" r="1.5" fill="#b9dfef"/></svg>SETTING</div>
  </nav>

  <svg class="chart" style="left:142px;top:69px" width="47" height="95" viewBox="0 0 47 95">
    <defs>
      <linearGradient id="heat-a" x1="0" y1="0" x2="0" y2="1">
        <stop offset="0" stop-color="var(--heat-hot)"/><stop offset=".35" stop-color="var(--heat-warm)"/>
        <stop offset=".7" stop-color="var(--heat-cool)"/><stop offset="1" stop-color="var(--heat-deep)"/>
      </linearGradient>
    </defs>
    <rect width="47" height="95" fill="url(#heat-a)"/>
    <g stroke="#ffffff" stroke-opacity=".35" stroke-width=".6"><path d="M11 0V95M23 0V95M35 0V95"/></g>
    <polyline points="0,48 6,42 11,44 16,36 21,38 27,30 32,33 38,26 43,31 47,28" fill="none" stroke="#f6e6a8" stroke-width="1"/>
    <polyline points="0,56 10,54 20,52 30,53 40,50 47,51" fill="none" stroke="#ffffff" stroke-opacity=".7" stroke-width=".6"/>
  </svg>
  <span class="chart-label" style="left:144px;top:172px">Jan</span>
  <span class="chart-label" style="left:156px;top:172px">Feb</span>
  <span class="chart-label" style="left:168px;top:172px">Mar</span>
  <span class="chart-label" style="left:179px;top:172px">Apr</span>

  <svg class="chart" style="left:150px;top:204px" width="39" height="98" viewBox="0 0 39 98">
    <defs>
      <linearGradient id="heat-b" x1="0" y1="0" x2="0" y2="1">
        <stop offset="0" stop-color="var(--heat-hot)"/><stop offset=".35" stop-color="var(--heat-warm)"/>
        <stop offset=".7" stop-color="var(--heat-cool)"/><stop offset="1" stop-color="var(--heat-deep)"/>
      </linearGradient>
    </defs>
    <rect width="39" height="98" fill="url(#heat-b)"/>
    <g stroke="#ffffff" stroke-opacity=".35" stroke-width=".6"><path d="M10 0V98M20 0V98M30 0V98"/></g>
    <polyline points="0,58 8,54 14,56 20,50 27,52 33,46 39,49" fill="none" stroke="#f6e6a8" stroke-width="1"/>
    <polyline points="0,62 12,60 24,61 39,58" fill="none" stroke="#ffffff" stroke-opacity=".7" stroke-width=".6"/>
  </svg>
  <span class="chart-label" style="left:136px;top:241px">2016</span>
  <span class="chart-label" style="left:136px;top:250px">2015</span>
  <span class="chart-label" style="left:136px;top:259px">2014</span>
  <span class="chart-label" style="left:152px;top:307px">Jan</span>
  <span class="chart-label" style="left:163px;top:307px">Feb</span>
  <span class="chart-label" style="left:174px;top:307px">Mar</span>
</section>

<!-- Messages screen -->
<section class="screen screen--messages">
  <div class="status-bar status-bar--light"><span>●●●○○ NOVA</span><span class="status-time">4:21 PM</span><span>100%<i class="battery"></i></span></div>
  <header class="app-header">
    <div class="menu-toggle"><span></span><span></span><span></span></div>
    <span class="nav-arrow nav-arrow--back">‹</span>
    <h1 class="header-title header-title--bold">MESSAGES</h1>
    <span class="nav-arrow nav-arrow--next">›</span>
  </header>
  <nav class="side-menu">
    <div class="menu-active"></div>
    <div class="menu-item" style="top:7px"><svg viewBox="0 0 10 10"><path d="M5 0 10 5H8.5V10H6V7H4V10H1.5V5H0z"/></svg>HOME</div>
    <div class="menu-sub" style="top:24px">How do you feel today ?</div>
    <div class="menu-sub" style="top:39px">TRACKING GRAPHS</div>
    <div class="menu-sub" style="top:54px">PERSONAL INFORMATION</div>
    <div class="menu-item" style="top:72px"><svg viewBox="0 0 10 10"><path d="M0 2H7V3H1V9H7V6H8V10H0zM9 0 10 1 5 6H4V5z"/></svg>ACTIVITY</div>
    <div class="menu-item" style="top:92px"><svg viewBox="0 0 10 10"><path d="M0 4 5 1 10 4V10H0zM1 5V9H9V5L5 7z"/></svg>MESSAGES</div>
    <div class="menu-item" style="top:113px"><svg viewBox="0 0 10 10"><circle cx="5" cy="3" r="2.5"/><path d="M0 10C0 6 10 6 10 10z"/></svg>PROFILE</div>
    <div class="menu-item" style="top:134px"><svg viewBox="0 0 10 10"><circle cx="5" cy="5" r="4"/><circle cx="5" cy="5" r="1.5" fill="#b9dfef"/></svg>SETTING</div>
  </nav>

  <div class="avatar" style="left:128px;top:49px;width:44px;height:51px" role="img" aria-label="Contact portrait photo"></div>
  <div class="bubble-tail" style="left:182px;top:53px"></div>
  <div class="bubble" style="left:144px;top:115px;width:50px;height:34px"><span class="bubble-time">5 minutes ago</span><span class="bubble-text">Thanks. Do you have</span></div>

  <div class="avatar" style="left:128px;top:172px;width:44px;height:51px" role="img" aria-label="Contact portrait photo"></div>
  <div class="bubble-tail" style="left:182px;top:176px"></div>
  <div class="bubble" style="left:141px;top:237px;width:53px;height:37px"><span class="bubble-time">7 minutes ago</span><span class="bubble-text">Thanks.</span></div>

  <div class="bubble" style="left:144px;top:302px;width:50px;height:40px"><span class="bubble-time">7 minutes ago</span><span class="bubble-text">Thanks.</span></div>
</section>

<!-- Personal information screen -->
<section class="screen screen--profile">
  <div class="status-bar"><span>●●●○○ NOVA</span><span class="status-time">4:21 PM</span><span>100%<i class="battery"></i></span></div>
  <header class="app-header">
    <div class="menu-toggle"><span></span><span></span><span></span></div>
    <span class="nav-arrow nav-arrow--back">‹</span>
    <h1 class="header-title">PERSONAL INFORMATION</h1>
    <span class="nav-arrow nav-arrow--next">›</span>
  </header>
  <nav class="side-menu">
    <div class="menu-active"></div>
    <div class="menu-item" style="top:7px"><svg viewBox="0 0 10 10"><path d="M5 0 10 5H8.5V10H6V7H4V10H1.5V5H0z"/></svg>HOME</div>
    <div class="menu-sub" style="top:24px">How do you feel today ?</div>
    <div class="menu-sub" style="top:39px">TRACKING GRAPHS</div>
    <div class="menu-sub" style="top:54px">PERSONAL INFORMATION</div>
    <div class="menu-item" style="top:72px"><svg viewBox="0 0 10 10"><path d="M0 2H7V3H1V9H7V6H8V10H0zM9 0 10 1 5 6H4V5z"/></svg>ACTIVITY</div>
    <div class="menu-item" style="top:92px"><svg viewBox="0 0 10 10"><path d="M0 4 5 1 10 4V10H0zM1 5V9H9V5L5 7z"/></svg>MESSAGES</div>
    <div class="menu-item" style="top:113px"><svg viewBox="0 0 10 10"><circle cx="5" cy="3" r="2.5"/><path d="M0 10C0 6 10 6 10 10z"/></svg>PROFILE</div>
    <div class="menu-item" style="top:134px"><svg viewBox="0 0 10 10"><circle cx="5" cy="5" r="4"/><circle cx="5" cy="5" r="1.5" fill="#b9dfef"/></svg>SETTING</div>
  </nav>

  <span class="profile-initial">M</span>
  <div class="avatar avatar--framed" style="left:155px;top:63px;width:40px;height:51px" role="img" aria-label="User profile photo"></div>

  <div class="action-button" style="top:122px"><svg viewBox="0 0 10 10"><path d="M1 6 6 1 9 4 4 9z"/></svg>Medication</div>
  <div class="action-button" style="top:141px"><svg viewBox="0 0 10 10"><path d="M1 1H9V10H1zM3 3V4H7V3zM3 5V6H7V5zM3 7V8H6V7z"/></svg>Consultation</div>
  <div class="action-button" style="top:161px"><svg viewBox="0 0 10 10"><path d="M5 9 1 5C-1 2 3 0 5 3 7 0 11 2 9 5z"/></svg>Health check</div>

  <h2 class="section-title" style="top:183px;font-weight:400">Friend and Family</h2>
  <ul class="contact-list" style="top:199px">
    <li>Mara Holt</li>
    <li>Dalton</li>
    <li>Owen Reyes</li>
  </ul>

  <h2 class="section-title" style="top:263px;font-weight:400">Most recently</h2>
  <ul class="contact-list" style="top:280px">
    <li>Depression</li>
    <li>Anxiaty</li>
  </ul>
</section>

</body>
</html>
```